WordPress Website Design for Multi-Brand Aviation Group (Unified Branding System)

Project Overview:
We are seeking a professional, modern WordPress website design for an aviation-focused umbrella company that owns and operates multiple subsidiary businesses. The goal is to create a cohesive visual system that clearly communicates that each company operates under the same parent organization, while still allowing each brand to maintain a slightly distinct identity.
This is not just a single website design—we are looking for a scalable design framework that can be applied across multiple aviation-related businesses.
Objectives:
- Establish a consistent, recognizable brand identity across all company websites
Clearly communicate the relationship between the parent company and its subsidiaries
-bCreate a clean, high-end corporate aviation aesthetic
- Ensure all designs are SEO-friendly and optimized for performance
- Allow flexibility for future expansion (additional subsidiaries)
- Target Audience:
- Corporate aviation clients
- Charter customers
- Students wishing to receive flight training
- Aircraft owners and operators
- Turbine aircraft training to meet insurance requirements
- Business professionals and high-net-worth individuals
- Aviation industry partners
Design Direction & Style:
We are looking for a premium, professional aviation feel—think clean, modern, and high-trust. The design should reflect the standards of corporate aviation: precision, safety, and sophistication.
Key style notes:
Minimalist but impactful layout
High-quality aviation photography (jets, interiors, operations, global travel)
Subtle motion/interaction (hover effects, transitions)
Clear typography hierarchy for readability and professionalism
Branding Requirements:
Incorporate the primary colors of the parent company logo across all designs
Website Structure (Core Pages):
Design a system that includes:
Home Page with the following links:
- About / Company Overview
- Aircraft Management
- Aircraft Acquisition
- Charter
- Pilot Services
- Trip Support
- Contact Page
Site should further include:
- Mobile-first responsive design
- Fast-loading, performance-optimized layouts
SEO & Technical Considerations:
- Design should support high-level SEO implementation:
- Clean layout structure that translates well to semantic HTML
- Proper heading hierarchy (H1, H2, H3)
- Space for keyword-rich content without clutter
- Optimized image placement (with alt text capability)
- Fast load times (lightweight design approach)
- Compatibility with WordPress SEO plugins (e.g., Yoast or Rank Math)
WordPress Requirements:
- Design should be easily built using WordPress (preferred builders: Elementor, Gutenberg, or similar)
- Reusable templates for scalability across multiple sites
- Easy for non-developers to update text and images
- Modular components (blocks/sections that can be reused across pages and sites)
- Navigation & UX:
- Simple, intuitive navigation
- Sticky header preferred
Style guide including:
- Colors
- Fonts
- Button styles
- Layout system
- Designs similar to high-end corporate aviation, private jet charter, or luxury service brands are preferred—clean, sharp, and premium without being overly flashy.
What We Want to Avoid:
- Overly busy layouts
- Generic templates with no brand identity
- Outdated or “stock” looking aviation designs
- Poor mobile responsiveness
Additional Notes:
We are building a long-term brand system, not just a one-off website. There is potential for ongoing work as we expand additional subsidiary sites.
We value designers who understand branding consistency across multiple business units and can create a scalable, professional system.
Include the attached main company logo "Vireton Aviation Group" and the "Member PJFO" logo on the main page.

```html
<!DOCTYPE html>
<html lang="en">
<head>
<meta charset="utf-8">
<title>Vireton Aviation Group</title>
<link rel="stylesheet" href="https://fonts.googleapis.com/css2?family=Teko:wght@400;500&family=Archivo:wght@400;500;600&display=swap">
<style>
:root{
  --blue:#0b4ea8;
  --blue-deep:#083f8c;
  --blue-bright:#1560c4;
  --ink:#111418;
  --text:#4a4f57;
  --muted:#6b7079;
  --white:#ffffff;
  --black:#050608;
}
*{margin:0;padding:0;box-sizing:border-box}
html,body{width:1200px;height:4648px;overflow:hidden}
body{position:relative;background:var(--white);font-family:"Archivo",Arial,sans-serif;color:var(--text)}
.abs{position:absolute}
.display{font-family:"Teko","Arial Narrow",sans-serif;font-weight:500;text-transform:uppercase;letter-spacing:.5px;line-height:1}
.btn{position:absolute;display:flex;align-items:center;justify-content:center;font-size:14px;font-weight:600;height:42px;padding:0 22px}
.btn-blue{background:var(--blue);color:var(--white)}
.btn-white{background:var(--white);color:var(--blue)}
svg.shape{position:absolute;left:0;width:1200px}

/* header */
.topbar{top:0;left:480px;width:720px;height:50px}
.topbar-text{top:0;right:110px;height:50px;display:flex;align-items:center;gap:22px;color:var(--white);font-size:13px}
.topbar-text span{display:flex;align-items:center;gap:10px}
.brand{top:40px;left:110px;color:var(--blue);font-family:"Archivo",sans-serif;font-weight:600;font-size:25px;display:flex;align-items:center;gap:10px;letter-spacing:.5px}
.brand i{display:block;width:14px;height:14px;background:var(--blue);border-radius:50%}
.nav{top:78px;left:419px;display:flex;gap:25px;font-size:13.5px;color:var(--ink)}

/* hero */
.hero-photo{top:122px;left:0;width:1200px;height:750px;background:radial-gradient(ellipse at 72% 30%,#c9d3df 0%,#7a7e86 14%,transparent 30%),linear-gradient(160deg,#2b2620 0%,#6a5332 35%,#3b3225 60%,#1c1914 100%)}
.hero-title{top:245px;left:110px;color:var(--white);font-size:60px;line-height:.98}
.hero-copy{top:433px;left:110px;width:470px;color:var(--white);font-size:16px;line-height:29px}

/* who */
.who-img1{top:945px;left:110px;width:227px;height:355px;background:linear-gradient(180deg,#c39a6a,#5a4632 60%,#2a221c);border:4px solid #fff;box-shadow:0 8px 30px rgba(0,0,0,.15)}
.who-img2{top:1125px;left:366px;width:231px;height:305px;background:linear-gradient(180deg,#6d6f9e,#b890b6 60%,#e5b8a5);border:4px solid #fff;box-shadow:0 8px 30px rgba(0,0,0,.15)}
.h2{color:var(--blue);font-size:48px}
.who-sub{top:1018px;left:670px;color:var(--ink);font-size:22px}
.para{font-size:14px;line-height:27.5px;color:var(--muted);text-align:justify}

/* services */
.svc-bg{top:1530px;left:0;width:1200px;height:940px;background:linear-gradient(180deg,rgba(255,255,255,.05),rgba(0,0,0,.08))}
.svc-title{top:1740px;left:0;width:1200px;text-align:center;color:var(--white);font-size:48px}
.svc-sub{top:1790px;left:300px;width:600px;text-align:center;color:var(--white);font-size:14px;line-height:24px}
.card{top:1872px;width:228px;height:350px;background:var(--white)}
.card-img{height:218px;border:4px solid #fff}
.card h3{font-family:"Teko",sans-serif;font-weight:500;text-transform:uppercase;color:var(--blue);font-size:23px;text-align:center;margin-top:12px;line-height:1}
.card p{font-size:12.5px;line-height:22px;text-align:center;color:var(--muted);padding:2px 14px 0}
.dots{top:2270px;left:570px;display:flex;gap:8px}
.dots i{display:block;width:9px;height:9px;background:rgba(255,255,255,.45)}
.dots i:first-child{background:#fff}

/* corporate */
.corp-list{top:2838px;left:152px;list-style:none;font-size:13.5px;color:var(--muted)}
.corp-list li{display:flex;align-items:center;gap:12px;height:35px}
.corp-img{top:2627px;left:600px;width:490px;height:458px;background:linear-gradient(180deg,#2a3038,#49525d 40%,#1e242b);border:4px solid #fff;box-shadow:0 8px 30px rgba(0,0,0,.2)}

/* video band */
.video-photo{top:3270px;left:0;width:1200px;height:760px;background:linear-gradient(180deg,#1b2028 0%,#3b4048 30%,#6a5a40 55%,#1a1c20 75%,#0f1115 100%)}
.play{top:3525px;left:110px;width:86px;height:86px;border-radius:50%;background:var(--white);display:flex;align-items:center;justify-content:center}
.video-title{top:3662px;left:110px;color:var(--white);font-size:80px;line-height:.92}
.video-sub{top:3835px;left:110px;color:var(--white);font-size:44px}

/* newsletter + footer */
.news-title{top:4118px;left:0;width:1200px;text-align:center;color:var(--white);font-size:36px}
.news-box{top:4170px;left:222px;width:754px;height:62px;background:rgba(255,255,255,.12);display:flex;align-items:center;justify-content:space-between;padding:0 28px;color:var(--white);font-size:15px}
.news-box span:last-child{display:flex;align-items:center;gap:14px}
.rule{left:110px;width:980px;height:1px;background:rgba(255,255,255,.25)}
.foot-brand{top:4355px;left:112px;color:var(--white);font-weight:600;font-size:20px;width:220px;line-height:26px}
.member{top:4440px;left:112px;color:var(--white);display:flex;align-items:center;gap:14px}
.member i{display:block;width:44px;height:44px;border-radius:50%;background:#fff}
.member small{display:block;font-size:12px}
.member b{font-weight:600;font-size:30px;line-height:1}
.foot-col{top:4318px;color:var(--white)}
.foot-col h4{font-family:"Teko",sans-serif;font-weight:500;text-transform:uppercase;font-size:32px;line-height:1;margin-bottom:10px}
.foot-col ul{list-style:none;font-size:13.5px}
.foot-col li{display:flex;align-items:center;gap:14px;height:35px}
.foot-col li.cont{padding-left:30px}
.gotop{top:4568px;left:985px;width:104px;height:32px;border-radius:16px;background:#fff;color:var(--blue);font-size:12px;display:flex;align-items:center;justify-content:center;gap:8px}
.copy{top:4616px;left:0;width:1200px;text-align:center;color:var(--white);font-size:12.5px}
</style>
</head>
<body>

<!-- Header -->
<header>
  <svg class="topbar abs" viewBox="0 0 720 50" preserveAspectRatio="none"><polygon points="30,0 720,0 720,50 0,50" fill="#0b4ea8"/></svg>
  <div class="topbar-text abs">
    <span><svg width="13" height="13" viewBox="0 0 24 24"><path fill="#fff" d="M6.6 10.8a15.1 15.1 0 0 0 6.6 6.6l2.2-2.2c.3-.3.7-.4 1-.2 1.1.4 2.3.6 3.6.6.6 0 1 .4 1 1V20c0 .6-.4 1-1 1A17 17 0 0 1 3 4c0-.6.4-1 1-1h3.5c.6 0 1 .4 1 1 0 1.3.2 2.5.6 3.6.1.3 0 .7-.2 1z"/></svg>Call Us: +1 (555) 014 2290</span>
    <span>|</span>
    <span><svg width="14" height="12" viewBox="0 0 24 20"><path fill="#fff" d="M2 0h20a2 2 0 0 1 2 2v1l-12 7L0 3V2a2 2 0 0 1 2-2zm-2 6 12 7 12-7v12a2 2 0 0 1-2 2H2a2 2 0 0 1-2-2z"/></svg>Email Us: info@viretonaviation.com</span>
  </div>
  <div class="brand abs"><i></i>VIRETON AVIATION GROUP</div>
  <nav class="nav abs"><span>About</span><span>Aircraft Management</span><span>Aircraft Acquisition</span><span>Charter</span><span>Pilot Services</span><span>Trip Support</span></nav>
</header>

<!-- Hero -->
<section>
  <div class="hero-photo abs" role="img" aria-label="Private jet flying above a sunlit mountain landscape"></div>
  <svg class="shape" style="top:600px;height:280px" viewBox="0 0 1200 280" preserveAspectRatio="none">
    <polygon points="0,190 1200,12 1200,40 0,262" fill="#0b4ea8"/>
    <polygon points="0,262 1200,40 1200,280 0,280" fill="#fff"/>
  </svg>
  <h1 class="hero-title display abs">Elevating Aviation<br>Ownership, Charter &amp;<br>Flight Solutions</h1>
  <p class="hero-copy abs">We delivers premium aviation services through a network of trusted subsidiaries specializing in aircraft management, charter, acquisitions, pilot services, &amp; trip support.</p>
  <span class="btn btn-blue" style="top:545px;left:110px">Explore Services</span>
  <span class="btn btn-white" style="top:545px;left:292px">Contact Us</span>
</section>

<!-- Who we are -->
<section>
  <svg class="shape" style="top:990px;height:370px" viewBox="0 0 1200 370"><path d="M340 4H457V130M230 310V360H366" fill="none" stroke="#0b4ea8" stroke-width="3"/></svg>
  <div class="who-img1 abs" role="img" aria-label="Pilot standing beside a jet at sunset"></div>
  <div class="who-img2 abs" role="img" aria-label="Passenger jet climbing into a pink evening sky"></div>
  <h2 class="h2 display abs" style="top:963px;left:670px">Who We Are</h2>
  <p class="who-sub display abs">One Aviation Group. Multiple Specialized Solutions.</p>
  <p class="para abs" style="top:1060px;left:670px;width:420px">Vireton Aviation Group is a modern aviation holding company built to serve aircraft owners, charter clients, flight students, and aviation professionals through a unified network of specialized businesses. We combine operational excellence, safety, and premium service standards across every division.</p>
  <p class="para abs" style="top:1226px;left:670px;width:420px">Sed ut perspiciatis unde omnis iste natus error sit voluptatem accusantium doloremque laudantium, totam rem aperiam, eaque ipsa quae ab illo inventore veritatis et quasi architecto beatae vitae dicta sunt explicabo.</p>
  <span class="btn btn-blue" style="top:1363px;left:670px">Explore More</span>
</section>

<!-- Services -->
<section>
  <svg class="shape" style="top:1450px;height:1120px" viewBox="0 0 1200 1120" preserveAspectRatio="none">
    <polygon points="0,255 1200,5 1200,80" fill="#050608"/>
    <polygon points="0,255 1200,80 1200,940 0,1025" fill="#0b4ea8"/>
    <polygon points="0,1025 1200,940 0,1110" fill="#050608"/>
  </svg>
  <div class="svc-bg abs" role="img" aria-label="Faint view of a parked jet behind the services"></div>
  <h2 class="svc-title display abs">Our Aviation Companies &amp; Services</h2>
  <p class="svc-sub abs">Sed ut perspiciatis unde omnis iste natus error sit voluptatem accusantium doloremque laudantium, totam rem aperiam, eaque ipsa quae ab illo inventore</p>
  <article class="card abs" style="left:110px"><div class="card-img" role="img" aria-label="Technician with tablet beside a jet in a hangar" style="background:linear-gradient(180deg,#3d4a5c,#8b96a4 55%,#2d3540)"></div><h3>Aircraft Management</h3><p>Sed ut perspiciatis unde omnis iste natus error sit voluptatem accusantium dolorem</p></article>
  <article class="card abs" style="left:360px"><div class="card-img" role="img" aria-label="Engineer inspecting a jet engine with digital overlay" style="background:linear-gradient(180deg,#1d3e52,#3f7d90 50%,#1b2a36)"></div><h3>Aircraft Acquisition</h3><p>Sed ut perspiciatis unde omnis iste natus error sit voluptatem accusantium dolorem</p></article>
  <article class="card abs" style="left:610px"><div class="card-img" role="img" aria-label="Private jet cabin with leather seats" style="background:linear-gradient(180deg,#4a3228,#cfc6bb 55%,#6b4a3a)"></div><h3>Charter Services</h3><p>Sed ut perspiciatis unde omnis iste natus error sit voluptatem accusantium dolorem</p></article>
  <article class="card abs" style="left:860px"><div class="card-img" role="img" aria-label="Pilots at the cockpit controls" style="background:linear-gradient(180deg,#1a2230,#3a4658 50%,#151b24)"></div><h3>Flight Training</h3><p>Sed ut perspiciatis unde omnis iste natus error sit voluptatem accusantium dolorem</p></article>
  <div class="dots abs"><i></i><i></i><i></i><i></i></div>
</section>

<!-- Corporate -->
<section>
  <h2 class="h2 display abs" style="top:2628px;left:110px;line-height:1.1">Corporate Aviation<br>Without Compromise</h2>
  <p class="para abs" style="top:2743px;left:110px;width:420px;text-align:left;font-size:13.5px;line-height:26px">From executive travel to aircraft ownership support, Vireton Aviation Group creates efficient, private, and dependable aviation experiences.</p>
  <ul class="corp-list abs">
    <li><svg width="15" height="15" viewBox="0 0 24 24"><rect x="2" y="2" width="20" height="20" rx="3" fill="none" stroke="#0b4ea8" stroke-width="2.5"/><path d="M7 12l4 4 8-9" fill="none" stroke="#0b4ea8" stroke-width="2.5"/></svg>Ut enim ad minima veniam, quis nostrum</li>
    <li><svg width="15" height="15" viewBox="0 0 24 24"><rect x="2" y="2" width="20" height="20" rx="3" fill="none" stroke="#0b4ea8" stroke-width="2.5"/><path d="M7 12l4 4 8-9" fill="none" stroke="#0b4ea8" stroke-width="2.5"/></svg>Exercitationem ullam corporis suscipit laboriosa</li>
    <li><svg width="15" height="15" viewBox="0 0 24 24"><rect x="2" y="2" width="20" height="20" rx="3" fill="none" stroke="#0b4ea8" stroke-width="2.5"/><path d="M7 12l4 4 8-9" fill="none" stroke="#0b4ea8" stroke-width="2.5"/></svg>Nisi ut aliquid ex ea commodi consequat</li>
    <li><svg width="15" height="15" viewBox="0 0 24 24"><rect x="2" y="2" width="20" height="20" rx="3" fill="none" stroke="#0b4ea8" stroke-width="2.5"/><path d="M7 12l4 4 8-9" fill="none" stroke="#0b4ea8" stroke-width="2.5"/></svg>Ut enim ad minima veniam, quis nostrum</li>
    <li><svg width="15" height="15" viewBox="0 0 24 24"><rect x="2" y="2" width="20" height="20" rx="3" fill="none" stroke="#0b4ea8" stroke-width="2.5"/><path d="M7 12l4 4 8-9" fill="none" stroke="#0b4ea8" stroke-width="2.5"/></svg>Exercitationem ullam corporis suscipit</li>
  </ul>
  <span class="btn btn-blue" style="top:3030px;left:110px">Explore More</span>
  <div class="corp-img abs" role="img" aria-label="Executive using a holographic tablet in a jet hangar"></div>
</section>

<!-- Video band -->
<section>
  <div class="video-photo abs" role="img" aria-label="Private jet on a runway at dusk under cloudy sky"></div>
  <svg class="shape" style="top:3170px;height:1478px" viewBox="0 0 1200 1478" preserveAspectRatio="none">
    <polygon points="0,0 1200,0 1200,5 0,260" fill="#fff"/>
    <polygon points="0,260 1200,5 1200,90 0,290" fill="#0b4ea8"/>
    <polygon points="0,730 1200,860 1200,1478 0,1478" fill="#0b4ea8"/>
    <polygon points="0,730 600,800 0,1100" fill="#0a48a0"/>
    <polygon points="1200,860 1200,1100 700,930" fill="#0d55b4"/>
  </svg>
  <div class="play abs"><svg width="22" height="24" viewBox="0 0 22 24"><polygon points="2,1 21,12 2,23" fill="#0b4ea8"/></svg></div>
  <h2 class="video-title display abs">One Aviation<br>Group.</h2>
  <p class="video-sub display abs">Multiple Specialized Solutions.</p>
</section>

<!-- Newsletter & Footer -->
<footer>
  <h2 class="news-title display abs">Subscribe To Our Newsletter</h2>
  <div class="news-box abs"><span>Enter Email Address</span><span>Subscribe Now <svg width="18" height="12" viewBox="0 0 18 12"><path d="M0 6h15M11 1l5 5-5 5" fill="none" stroke="#fff" stroke-width="2"/></svg></span></div>
  <div class="rule abs" style="top:4280px"></div>
  <div class="foot-brand abs">VIRETON AVIATION GROUP</div>
  <div class="member abs"><i></i><div><small>member of</small><b>PJFO</b></div></div>
  <div class="foot-col abs" style="left:410px">
    <h4>Quick Links</h4>
    <ul>
      <li><svg width="14" height="14" viewBox="0 0 16 16"><circle cx="8" cy="8" r="8" fill="#fff"/><path d="M6 4l4 4-4 4" fill="none" stroke="#0b4ea8" stroke-width="2"/></svg>Home</li>
      <li><svg width="14" height="14" viewBox="0 0 16 16"><circle cx="8" cy="8" r="8" fill="#fff"/><path d="M6 4l4 4-4 4" fill="none" stroke="#0b4ea8" stroke-width="2"/></svg>About Vireton Aviation</li>
      <li><svg width="14" height="14" viewBox="0 0 16 16"><circle cx="8" cy="8" r="8" fill="#fff"/><path d="M6 4l4 4-4 4" fill="none" stroke="#0b4ea8" stroke-width="2"/></svg>Trip Support</li>
      <li><svg width="14" height="14" viewBox="0 0 16 16"><circle cx="8" cy="8" r="8" fill="#fff"/><path d="M6 4l4 4-4 4" fill="none" stroke="#0b4ea8" stroke-width="2"/></svg>Careers</li>
      <li><svg width="14" height="14" viewBox="0 0 16 16"><circle cx="8" cy="8" r="8" fill="#fff"/><path d="M6 4l4 4-4 4" fill="none" stroke="#0b4ea8" stroke-width="2"/></svg>Contact Us</li>
    </ul>
  </div>
  <div class="foot-col abs" style="left:640px">
    <h4>Services</h4>
    <ul>
      <li><svg width="14" height="14" viewBox="0 0 16 16"><circle cx="8" cy="8" r="8" fill="#fff"/><path d="M6 4l4 4-4 4" fill="none" stroke="#0b4ea8" stroke-width="2"/></svg>Aircraft Management</li>
      <li><svg width="14" height="14" viewBox="0 0 16 16"><circle cx="8" cy="8" r="8" fill="#fff"/><path d="M6 4l4 4-4 4" fill="none" stroke="#0b4ea8" stroke-width="2"/></svg>Aircraft Acquisition</li>
      <li><svg width="14" height="14" viewBox="0 0 16 16"><circle cx="8" cy="8" r="8" fill="#fff"/><path d="M6 4l4 4-4 4" fill="none" stroke="#0b4ea8" stroke-width="2"/></svg>Charter</li>
      <li><svg width="14" height="14" viewBox="0 0 16 16"><circle cx="8" cy="8" r="8" fill="#fff"/><path d="M6 4l4 4-4 4" fill="none" stroke="#0b4ea8" stroke-width="2"/></svg>Pilot Services</li>
    </ul>
  </div>
  <div class="foot-col abs" style="left:853px">
    <h4>Contact Us</h4>
    <ul>
      <li><svg width="14" height="14" viewBox="0 0 24 24"><path fill="#fff" d="M12 2 1 12h3v9h6v-6h4v6h6v-9h3z"/></svg>480 Harbor Field Road</li>
      <li class="cont">Suite 12, Larkston, NC 28999</li>
      <li class="cont">United States</li>
      <li><svg width="14" height="12" viewBox="0 0 24 20"><path fill="#fff" d="M2 0h20a2 2 0 0 1 2 2v1l-12 7L0 3V2a2 2 0 0 1 2-2zm-2 6 12 7 12-7v12a2 2 0 0 1-2 2H2a2 2 0 0 1-2-2z"/></svg>info@viretonaviation.com</li>
      <li><svg width="14" height="14" viewBox="0 0 24 24"><rect x="1" y="1" width="22" height="22" rx="4" fill="#fff"/><path fill="#0b4ea8" d="M8 6l2 3-1.5 1.5a9 9 0 0 0 5 5L15 14l3 2-1 3c-6 0-11-5-11-11z"/></svg>+1 555 014 2290</li>
    </ul>
  </div>
  <div class="rule abs" style="top:4585px"></div>
  <div class="gotop abs"><svg width="10" height="7" viewBox="0 0 10 7"><path d="M1 6l4-4 4 4" fill="none" stroke="#0b4ea8" stroke-width="2"/></svg>Go Top</div>
  <p class="copy abs">(C) Copyright 2026 | All Rights Reserved</p>
</footer>

</body>
</html>
```